Quiet Harbor Prints gallery website

I need a Website for a gallery with a shopify integration or maybe even better also compatible with squarespace.
the website should have following riders: Künstler, Veranstaltungen, Shop, About Us.
some nice examples for inspiration of the website architecture are:
https://www.lindwerkraum.com/
https://www.plattenbau-salon.com/de/
https://moorlichtraum.de/
It should be easy for us to make adaptations and fill the website with new content.
Attached there is the CI an logo for the brand.
Target Market(s)
Art Collectors,
Industry/Entity Type
artgallery
Coding
Coded - Design and coding required
Number of Pages Required
3 page
Font styles to use
Look and feel

```html
<!DOCTYPE html>
<html lang="en">
<head>
<meta charset="utf-8">
<title>Quiet Harbor Prints — Gallery</title>
<link rel="stylesheet" href="https://fonts.googleapis.com/css2?family=Titillium+Web:wght@300;400;600&family=Lato:wght@400;700&display=swap">
<style>
:root{
  --ink:#1d1d1d;
  --text:#3a3a3a;
  --muted:#6b6b6b;
  --white:#ffffff;
  --night:#141414;
  --night-2:#1c1a1c;
  --plum:#3a1a33;
  --olive:#3b3a1c;
  --brand-red:#c8202a;
  --line:#d8d8d8;
  --display:'Titillium Web', sans-serif;
  --body:'Lato', sans-serif;
}
*{box-sizing:border-box;margin:0;padding:0}
html,body{width:1200px;height:4800px;overflow:hidden}
body{position:relative;background:var(--white);font-family:var(--body);color:var(--text)}
section,header,footer{position:absolute;left:0;width:1200px}
.abs{position:absolute}
.media{position:absolute}

/* header */
.site-header{top:0;height:104px;background:var(--white)}
.brand{position:absolute;display:flex;align-items:center;gap:10px;font-family:var(--display);font-weight:400;color:var(--ink);letter-spacing:.5px}
.brand-mark{width:12px;height:12px;background:var(--brand-red)}
.site-header .brand{left:84px;top:38px;font-size:17px;text-transform:uppercase}
.main-nav{position:absolute;top:43px;left:603px;display:flex;gap:0;font-family:var(--display);font-size:14px;letter-spacing:1px;color:var(--ink)}
.main-nav a{position:absolute;white-space:nowrap;color:inherit;text-decoration:none}
.header-icons{position:absolute;top:42px;left:1008px}
.header-icons svg{position:absolute;top:0}

/* hero */
.hero{top:104px;height:554px;overflow:hidden}
.hero-photo{inset:0;background:
  linear-gradient(90deg,rgba(20,12,6,.55) 0%,rgba(20,12,6,.15) 45%,rgba(0,0,0,0) 70%),
  linear-gradient(180deg,#e7e4de 0%,#cfc7ba 38%,#9e6a3e 62%,#6e4221 100%)}
.hero-kicker{left:84px;top:240px;font-family:var(--display);font-size:19px;color:var(--white);letter-spacing:.5px}
.hero-title{left:84px;top:270px;font-family:var(--display);font-weight:300;font-size:41px;line-height:52px;color:var(--white);letter-spacing:1px}
.btn-outline{position:absolute;left:84px;top:401px;width:170px;height:41px;border:1px solid var(--white);color:var(--white);font-size:12px;letter-spacing:2.5px;display:flex;align-items:center;justify-content:center;font-family:var(--body)}
.slider-dots{left:513px;top:505px;display:flex;gap:14px}
.slider-dots span{width:50px;height:2px;background:rgba(255,255,255,.45)}
.slider-dots span.active{background:var(--white)}

/* intro */
.intro{top:658px;height:936px}
.section-title{position:absolute;left:0;width:1200px;text-align:center;font-family:var(--display);font-weight:300;color:var(--ink)}
.intro-title{top:44px;font-size:32px;line-height:41px;text-transform:uppercase}
.intro-text{position:absolute;left:200px;width:800px;top:142px;text-align:center;font-size:13.5px;line-height:28px;color:var(--text)}
.events-title{top:220px;font-size:27px;font-weight:400;text-transform:uppercase}
.event-card{position:absolute;left:158px;width:883px;display:flex;flex-direction:column;align-items:center;justify-content:center;color:var(--white);text-align:center}
.event-card .media{inset:0}
.event-card .date,.event-card .event-name{position:relative}
.event-card .date{font-size:13px;letter-spacing:.5px;margin-bottom:8px}
.event-card .event-name{font-family:var(--display);font-weight:300;font-size:28px;line-height:37px}
.event-one{top:266px;height:274px}
.event-one .media{background:linear-gradient(100deg,#b8afa2 0%,#a79f92 40%,#8e8a83 60%,#b3ab9f 100%)}
.event-two{top:563px;height:249px}
.event-two .media{background:linear-gradient(100deg,#b3aea6 0%,#9f9b95 45%,#7d7a76 60%,#aaa49c 100%)}
.btn-solid{position:absolute;height:42px;background:var(--night);color:var(--white);font-size:12.5px;letter-spacing:2.5px;display:flex;align-items:center;justify-content:center}
.intro .btn-solid{left:505px;top:832px;width:188px}

/* artwork */
.artwork{top:1594px;height:973px;background:
  radial-gradient(ellipse 520px 420px at 1120px 180px,rgba(88,30,78,.55),rgba(0,0,0,0) 70%),
  radial-gradient(ellipse 500px 400px at 1150px 850px,rgba(70,25,60,.45),rgba(0,0,0,0) 70%),
  var(--night)}
.eyebrow{position:absolute;font-size:10.5px;letter-spacing:.3px;color:var(--white);text-transform:uppercase;font-weight:700}
.artwork .eyebrow{left:84px;top:57px}
.artwork-title{left:84px;top:82px;font-family:var(--display);font-weight:300;font-size:34px;line-height:42px;color:var(--white);text-transform:uppercase;letter-spacing:.5px}
.artwork-intro{left:545px;top:68px;width:560px;font-size:13px;line-height:27px;color:#e8e8e8}
.art-item{position:absolute;width:320px;text-align:center}
.art-item .media{position:relative;width:320px;height:234px}
.art-item .tag{margin-top:18px;font-size:10.5px;letter-spacing:2px;color:var(--white);font-weight:700}
.art-item .name{margin-top:6px;font-family:var(--display);font-size:19px;color:var(--white);letter-spacing:.5px}
.add-to-cart{position:absolute;left:0;top:0;width:320px;height:234px;display:flex;align-items:center;justify-content:center;gap:8px;color:var(--white);font-size:12px;letter-spacing:2px;background:rgba(0,0,0,.45)}
.link-underline{position:absolute;left:563px;top:895px;font-size:12.5px;letter-spacing:2.5px;color:var(--white);padding-bottom:5px;border-bottom:1px solid var(--white)}

/* popular */
.popular{top:2567px;height:635px;background:linear-gradient(180deg,#ffffff 0%,#ffffff 60%,#f7f3ea 100%)}
.popular-title{top:48px;font-size:32px}
.popular-text{position:absolute;left:270px;width:660px;top:98px;text-align:center;font-size:13.5px;line-height:24px;color:var(--text)}
.framed{position:absolute;top:174px;width:217px;text-align:center}
.frame{width:217px;height:294px;background:#111;padding:14px}
.frame .media{position:relative;width:100%;height:100%}
.framed .name{margin-top:16px;font-family:var(--display);font-size:19px;color:var(--ink);letter-spacing:1px;text-transform:uppercase}
.popular .btn-solid{left:523px;top:537px;width:153px}

/* newsletter */
.newsletter{top:3202px;height:275px;background:
  radial-gradient(ellipse 420px 300px at 0 300px,rgba(90,88,30,.75),rgba(0,0,0,0) 75%),
  radial-gradient(ellipse 500px 320px at 1200px 120px,rgba(80,30,72,.6),rgba(0,0,0,0) 75%),
  var(--night-2)}
.newsletter .eyebrow{left:198px;top:90px}
.newsletter-title{left:198px;top:108px;font-family:var(--display);font-weight:300;font-size:34px;color:var(--white);letter-spacing:.5px}
.newsletter-note{left:198px;top:165px;font-size:11px;font-weight:700;color:var(--white)}
.signup{position:absolute;left:510px;top:121px;width:476px;height:43px;background:var(--white);display:flex;align-items:center;justify-content:space-between;padding:0 14px}
.signup span{font-size:13px;color:var(--muted)}

/* projects */
.projects{top:3477px;height:947px}
.projects-title{top:60px;font-size:32px;text-transform:uppercase}
.projects-text{position:absolute;left:0;width:1200px;top:106px;text-align:center;font-size:14px;color:var(--text)}
.project-main{left:158px;top:154px;width:883px;height:354px;background:linear-gradient(90deg,#ede7dd 0%,#d9d0c2 45%,#c8b9a2 66%,#1d2430 72%,#2b3340 100%)}
.project-caption{left:185px;top:460px;font-family:var(--display);font-weight:300;font-size:27px;color:var(--white)}
.project-a{left:158px;top:537px;width:429px;height:272px;background:linear-gradient(180deg,#3a3430 0%,#9a6a4a 50%,#d99a6a 65%,#5a3b2a 100%)}
.project-b{left:613px;top:537px;width:428px;height:272px;background:linear-gradient(180deg,#5a5650 0%,#7e6a55 50%,#b98e64 68%,#4c3a2b 100%)}
.projects .btn-solid{left:523px;top:853px;width:154px}

/* footer */
.site-footer{top:4424px;height:376px;background:
  radial-gradient(ellipse 360px 260px at 0 380px,rgba(80,78,28,.7),rgba(0,0,0,0) 75%),
  var(--night);color:#d8d8d8}
.site-footer .brand{left:84px;top:120px;width:236px;justify-content:center;color:var(--white);font-size:21px;text-transform:uppercase;letter-spacing:1px}
.social{position:absolute;left:132px;top:232px;display:flex;gap:34px}
.social span{width:16px;height:16px;border:1.5px solid var(--white);border-radius:50%}
.footer-col{position:absolute;top:82px}
.footer-col h3{font-family:var(--display);font-weight:400;font-size:17px;color:var(--white);letter-spacing:1px;text-transform:uppercase;margin-bottom:17px}
.footer-col ul{list-style:none}
.footer-col li{font-size:13.5px;line-height:21px;color:#d0d0d0}
.links li{margin-bottom:15px}
.contact li{display:flex;gap:12px;margin-bottom:14px}
.contact svg{flex:none;margin-top:3px}
.footer-rule{position:absolute;left:84px;top:304px;width:1030px;height:1px;background:#3a3a3a}
.copyright{position:absolute;left:0;width:1200px;top:335px;text-align:center;font-size:12px;color:#9a9a9a}
.copyright strong{color:var(--white);font-weight:400}
.payments{position:absolute;left:918px;top:331px;display:flex;gap:17px}
.payments span{width:37px;height:24px;border-radius:3px;background:#e6e6e6}
</style>
</head>
<body>

<header class="site-header">
  <div class="brand"><span class="brand-mark"></span>Quiet Harbor Prints</div>
  <nav class="main-nav">
    <a style="left:0">ARTISTS</a>
    <a style="left:109px">EVENTS</a>
    <a style="left:214px">SHOP</a>
    <a style="left:302px">ABOUT US</a>
  </nav>
  <div class="header-icons">
    <svg style="left:0" width="18" height="18" viewBox="0 0 18 18" fill="none" stroke="#1d1d1d" stroke-width="1.6"><circle cx="7.5" cy="7.5" r="5.5"/><path d="M11.5 11.5l5 5"/></svg>
    <svg style="left:44px" width="18" height="18" viewBox="0 0 18 18" fill="none" stroke="#1d1d1d" stroke-width="1.6"><path d="M9 15.5S2 11 2 6.3A3.6 3.6 0 0 1 9 4.7a3.6 3.6 0 0 1 7 1.6C16 11 9 15.5 9 15.5z"/></svg>
    <svg style="left:86px" width="20" height="18" viewBox="0 0 20 18" fill="none" stroke="#1d1d1d" stroke-width="1.6"><path d="M1 1.5h3l2.2 10h10l2-7H5"/><circle cx="7.5" cy="15.5" r="1.3"/><circle cx="15" cy="15.5" r="1.3"/></svg>
  </div>
</header>

<section class="hero">
  <div class="media hero-photo" role="img" aria-label="Photo of a bright gallery hall with framed paintings and a standing sculpture on a plinth"></div>
  <p class="abs hero-kicker">BEGIN AN EXPLORATION THROUGH</p>
  <h1 class="abs hero-title">A GALLERY SHOWCASING<br>ARTIST CREATIVIY</h1>
  <a class="btn-outline">EXPLORE</a>
  <div class="abs slider-dots"><span class="active"></span><span></span><span></span></div>
</section>

<section class="intro">
  <h2 class="section-title intro-title">The gallery for urban art and contemporary<br>art in Hamburg!</h2>
  <p class="intro-text">Lorem ipsum dolor sit amet, consectetur adipiscing elit, sed do eiusmod tempor incididunt ut labore et dolore magna aliqua. Quis ipsum suspendisse ultrices gravida. Risus commodo viverra maecenas accumsan lacus vel facilisis.</p>
  <h2 class="section-title events-title">Upcoming Events</h2>
  <article class="event-card event-one">
    <div class="media" role="img" aria-label="Collage artwork with sunflowers and leaves on a muted beige textured background"></div>
    <p class="date">MAR. 18,2024</p>
    <h3 class="event-name">Proin scelerisque dolor vitae<br>augue condimentum</h3>
  </article>
  <article class="event-card event-two">
    <div class="media" role="img" aria-label="Monochrome geometric collage artwork with diamonds, lines and dots on grey paper"></div>
    <p class="date">APR. 18,2024</p>
    <h3 class="event-name">Proin scelerisque dolor vitae<br>augue condimentum</h3>
  </article>
  <a class="btn-solid">VIEW ALL EVENTS</a>
</section>

<section class="artwork">
  <p class="eyebrow">New Artwork</p>
  <h2 class="abs artwork-title">Unveiling our<br>exclusive artwork</h2>
  <p class="abs artwork-intro">Class aptent taciti sociosqu ad litora torquent per conubia nostra, per inceptos himenaeos. Vestibulum non congue ligula, ut sollicitudin arcut taciti sociosqu ad litora torquent per conubia nostra, per inceptos himenaeos.</p>

  <div class="art-item" style="left:84px;top:186px">
    <div class="media" role="img" aria-label="Abstract painting of teal waves and orange spheres under a pale moon" style="background:linear-gradient(160deg,#1e2a33 0%,#e0b070 40%,#2f8a8a 60%,#e07a2a 80%,#2a1e1a 100%)"></div>
    <p class="tag">CREATIVE</p><p class="name">MODERN ART</p>
  </div>
  <div class="art-item" style="left:440px;top:186px">
    <div class="media" role="img" aria-label="Cubist style abstract painting in dark red, ochre and teal" style="background:linear-gradient(135deg,#3a1e1a 0%,#6a2a22 40%,#8a6a2a 70%,#1f2a2a 100%)"></div>
    <div class="add-to-cart"><svg width="16" height="14" viewBox="0 0 20 18" fill="none" stroke="#fff" stroke-width="1.8"><path d="M1 1.5h3l2.2 10h10l2-7H5"/><circle cx="7.5" cy="15.5" r="1.3"/><circle cx="15" cy="15.5" r="1.3"/></svg>ADD TO CART</div>
    <p class="tag">CREATIVE</p><p class="name">MODERN ART</p>
  </div>
  <div class="art-item" style="left:795px;top:186px">
    <div class="media" role="img" aria-label="Painting of a single white flower on a soft peach background" style="background:radial-gradient(circle at 30% 40%,#faf4ef 0%,#f2d6c8 40%,#eac4b2 100%)"></div>
    <p class="tag">CREATIVE</p><p class="name">MODERN ART</p>
  </div>

  <div class="art-item" style="left:84px;top:550px">
    <div class="media" role="img" aria-label="Double exposure artwork blending a figure's back with a misty hill landscape" style="background:linear-gradient(180deg,#d9d6d0 0%,#a9a39a 40%,#6e6a4a 70%,#d9d5cd 100%)"></div>
    <p class="tag">CREATIVE</p><p class="name">MODERN ART</p>
  </div>
  <div class="art-item" style="left:440px;top:550px">
    <div class="media" role="img" aria-label="Ink splash painting of a red autumn tree over pale pink mountains" style="background:radial-gradient(circle at 50% 40%,#c0401e 0%,#e08a5a 30%,#f3e6de 65%,#eee4dc 100%)"></div>
    <p class="tag">CREATIVE</p><p class="name">MODERN ART</p>
  </div>
  <div class="art-item" style="left:795px;top:550px">
    <div class="media" role="img" aria-label="Ink painting of a lone tree and birds above a golden field" style="background:linear-gradient(180deg,#e4e2de 0%,#c9c6c0 45%,#3a3a34 65%,#b19a3a 85%,#2a2a24 100%)"></div>
    <p class="tag">CREATIVE</p><p class="name">MODERN ART</p>
  </div>

  <a class="link-underline">VIEW ALL</a>
</section>

<section class="popular">
  <h2 class="section-title popular-title">Our Popular Art</h2>
  <p class="popular-text">Etiam ut libero pulvinar, imperdiet enim vel, euismod dui. Nunc nec feugiat ex. Praesent at eros lectus. Duis iaculis posuere arcu quis pretium.</p>
  <div class="framed" style="left:84px"><div class="frame"><div class="media" role="img" aria-label="Framed print of a silhouette filled with snowy mountains and flowers on mustard yellow" style="background:linear-gradient(180deg,#d9b44a 0%,#e8e2d6 45%,#2a2a2a 75%,#d9b44a 100%)"></div></div><p class="name">Creative Art</p></div>
  <div class="framed" style="left:355px"><div class="frame"><div class="media" role="img" aria-label="Framed print of a head profile with a coral tree and red clouds" style="background:linear-gradient(180deg,#2a3a44 0%,#c0402a 35%,#3aa0a0 60%,#d9b0b0 100%)"></div></div><p class="name">Creative Art</p></div>
  <div class="framed" style="left:626px"><div class="frame"><div class="media" role="img" aria-label="Framed print of an abstract grey face shape under a crescent moon" style="background:linear-gradient(160deg,#1e2a3a 0%,#7a8a9a 40%,#c9c9c9 60%,#c8a04a 100%)"></div></div><p class="name">Creative Art</p></div>
  <div class="framed" style="left:897px"><div class="frame"><div class="media" role="img" aria-label="Framed print of a pink floral composition with butterflies on pale blue" style="background:radial-gradient(circle at 50% 50%,#e07080 0%,#e8a080 35%,#bcd6d6 70%,#a9c9cc 100%)"></div></div><p class="name">Creative Art</p></div>
  <a class="btn-solid">VIEW ALL</a>
</section>

<section class="newsletter">
  <p class="eyebrow">Subscribe to</p>
  <h2 class="abs newsletter-title">OUR NEWSLETTER</h2>
  <p class="abs newsletter-note">With our newsletter you won't miss any exhibitions.</p>
  <div class="signup"><span>Email Address</span>
    <svg width="20" height="14" viewBox="0 0 20 14" fill="none" stroke="#333" stroke-width="1.6"><path d="M1 7h17M12 1l6 6-6 6"/></svg></div>
</section>

<section class="projects">
  <h2 class="section-title projects-title">Our Latest Projects</h2>
  <p class="projects-text">Quisque lacinia elit nulla, non congue dui dignissim at</p>
  <div class="media project-main" role="img" aria-label="Photo of a gallery hall hung with colourful abstract paintings"></div>
  <p class="abs project-caption">Hall of Frame</p>
  <div class="media project-a" role="img" aria-label="Photo of a long gallery corridor with vivid paintings and a polished wooden floor"></div>
  <div class="media project-b" role="img" aria-label="Photo of a warm-lit exhibition hall with large paintings and a central bench"></div>
  <a class="btn-solid">VIEW ALL</a>
</section>

<footer class="site-footer">
  <div class="brand"><span class="brand-mark"></span>Quiet Harbor Prints</div>
  <div class="social"><span></span><span></span><span></span><span></span></div>

  <div class="footer-col contact" style="left:423px">
    <h3>Contact Info</h3>
    <ul>
      <li><svg width="14" height="14" viewBox="0 0 14 14" fill="none" stroke="#fff" stroke-width="1.4"><path d="M7 1l6 6-6 6-6-6z"/><circle cx="7" cy="7" r="1.6"/></svg><span>No-12 B, Larkspur Lane,<br>Eastfield, ST, Nowhere</span></li>
      <li><svg width="14" height="14" viewBox="0 0 14 14" fill="none" stroke="#fff" stroke-width="1.4"><path d="M2 1.5h3l1.3 3-1.8 1.2a8 8 0 0 0 3.8 3.8l1.2-1.8 3 1.3v3A1.5 1.5 0 0 1 11 13 10 10 0 0 1 1 3a1.5 1.5 0 0 1 1-1.5z"/></svg><span>1800-555-0142</span></li>
      <li><svg width="14" height="12" viewBox="0 0 14 12" fill="none" stroke="#fff" stroke-width="1.4"><rect x="1" y="1" width="12" height="10"/><path d="M1 1l6 5 6-5"/></svg><span>info@quietharborprints.example</span></li>
    </ul>
  </div>
  <div class="footer-col links" style="left:762px">
    <h3>Quick Links</h3>
    <ul><li>Artists</li><li>Events</li><li>Shop</li><li>About Us</li></ul>
  </div>
  <div class="footer-col links" style="left:990px">
    <h3>Useful Links</h3>
    <ul><li>My Account</li><li>Terms of use</li><li>Privacy Policy</li><li>Payment Methods</li></ul>
  </div>

  <div class="footer-rule"></div>
  <p class="copyright">© 2024 <strong>QUIET HARBOR PRINTS HAMBURG</strong>. All right reserved</p>
  <div class="payments"><span></span><span></span><span></span><span></span></div>
</footer>

</body>
</html>
```